Brivolt Technologies business card design

We need a business card designed with our new logo. it would be great if the card could communicate it is a technology based company.

Target Market(s)

system integrators

Industry/Entity Type

technology, IOT

Contact Information for Business Card

Name, designation, Address, telephone number, email address

Requirements
Must have
• logo and company name
Nice to have
• something to do with technology

```html
<!DOCTYPE html>
<html lang="en">
<head>
<meta charset="utf-8">
<title>Brivolt Technologies – Business Card</title>
<link href="https://fonts.googleapis.com/css2?family=Exo+2:wght@600&family=Roboto:wght@400&display=swap" rel="stylesheet">
<style>
  :root {
    --page-bg: #7a5b3e;
    --card-light: #ffffff;
    --card-dark: #3e3e40;
    --ink: #3d3d3f;
    --accent: #f39019;
    --white: #ffffff;
  }
  * { margin: 0; padding: 0; box-sizing: border-box; }
  html, body { width: 900px; height: 1200px; overflow: hidden; }
  body { background: var(--page-bg); position: relative; font-family: "Roboto", sans-serif; }

  .card {
    position: absolute;
    left: 86px;
    width: 735px;
    height: 431px;
    box-shadow: 0 4px 14px rgba(0,0,0,0.35);
  }
  .card--front { top: 136px; background: var(--card-light); }
  .card--back { top: 633px; background: var(--card-dark); }

  .brand {
    position: absolute;
    left: 0; right: 0;
    display: flex;
    align-items: center;
    justify-content: center;
    gap: 16px;
  }
  .brand__square { width: 34px; height: 34px; background: var(--accent); flex: none; }
  .brand__name {
    font-family: "Exo 2", sans-serif;
    font-weight: 600;
    font-size: 44px;
    letter-spacing: 1px;
    line-height: 1;
    color: var(--ink);
  }
  .card--front .brand { top: 106px; }
  .card--back .brand { top: 190px; }
  .card--back .brand__name { color: var(--white); font-size: 50px; }

  .person {
    position: absolute;
    right: 400px;
    top: 290px;
    text-align: right;
  }
  .person__name {
    font-family: "Exo 2", sans-serif;
    font-weight: 600;
    font-size: 28px;
    color: var(--accent);
    line-height: 1.1;
  }
  .person__role { font-size: 18px; color: var(--ink); margin-top: 4px; letter-spacing: 0.3px; }

  .divider {
    position: absolute;
    left: 353px;
    top: 265px;
    width: 1.5px;
    height: 108px;
    background: var(--ink);
  }

  .contact {
    position: absolute;
    left: 370px;
    top: 266px;
    font-size: 17.5px;
    color: var(--ink);
    letter-spacing: 0.3px;
    line-height: 21px;
    list-style: none;
  }
  .contact__line { display: flex; align-items: center; }
  .contact__line--icon { margin-top: 2px; }
  .contact__icon { width: 13px; height: 13px; margin-right: 11px; fill: var(--accent); flex: none; }
</style>
</head>
<body>

  <section class="card card--front" aria-label="Business card front">
    <div class="brand">
      <span class="brand__square"></span>
      <span class="brand__name">Brivolt Technologies</span>
    </div>

    <div class="person">
      <p class="person__name">Marcus Ellery</p>
      <p class="person__role">Managing Director</p>
    </div>

    <div class="divider"></div>

    <ul class="contact">
      <li class="contact__line">48 Harbour Lane, Suite B</li>
      <li class="contact__line">Leeds, UK LS1 4QT</li>
      <li class="contact__line contact__line--icon">
        <svg class="contact__icon" viewBox="0 0 16 16" aria-hidden="true"><path d="M3.6 1.2l2.3 2.8-1.4 1.6c.9 2 2.5 3.6 4.5 4.5l1.6-1.4 2.8 2.3-1.2 2.6C6.6 13.4 2.6 9.4 1 3.8z"/></svg>
        000-000-0000
      </li>
      <li class="contact__line contact__line--icon">
        <svg class="contact__icon" viewBox="0 0 16 16" aria-hidden="true"><path d="M1 3h14v1.4L8 9 1 4.4z"/><path d="M1 6.2l7 4.6 7-4.6V13H1z"/></svg>
        info@brivolttech.com
      </li>
      <li class="contact__line contact__line--icon">
        <svg class="contact__icon" viewBox="0 0 16 16" aria-hidden="true"><circle cx="8" cy="8" r="6.5" fill="none" stroke="#f39019" stroke-width="1.3"/><ellipse cx="8" cy="8" rx="2.8" ry="6.5" fill="none" stroke="#f39019" stroke-width="1.1"/><path d="M1.5 8h13M2.5 5h11M2.5 11h11" stroke="#f39019" stroke-width="1"/></svg>
        www.brivolttech.com
      </li>
    </ul>
  </section>

  <section class="card card--back" aria-label="Business card back">
    <div class="brand">
      <span class="brand__square"></span>
      <span class="brand__name">Brivolt Technologies</span>
    </div>
  </section>

</body>
</html>
```